13 Varno - new website design project

Our company Varno Electrical is developing a new lead generation website focused on Electrical, LED Lighting and Solar Power. We need a high converting website.

Example of our current website is www.varnoelectrical-example.com.au You can take content from this website for this new design. Our colours are red, black and white. For our new website we would like to promote Varno, Spark Every Day. Please listen to the jingle.

The below link is the company jingle that we have developed.
http://www.tunecraftdemo.com.au/vrn-tc-v1/

The key for this brief is to generate leads for Electrical, LED Lighting (for commercial) and Solar Power & Storage.

Target Market(s)

Business owners in Melbourne Victoria

Number of Pages Required

4 page

Colors
ec1f27
ffffff

Requirements
Must have
• This page must be clean, be in line with company branding and a high converting lead website.

```html
<!DOCTYPE html>
<html lang="en">
<head>
<meta charset="utf-8">
<title>Varno Electrical – Spark Every Day</title>
<link href="https://fonts.googleapis.com/css2?family=Rajdhani:wght@500;600;700&family=Open+Sans:wght@400;600;700&display=swap" rel="stylesheet">
<style>
:root{
  --red:#ec1f27;
  --black:#1c1c1e;
  --dark:#2e3035;
  --ink:#333;
  --muted:#777;
  --line:#d9d9d9;
  --panel:#ebebeb;
  --nav:#e4e4e4;
  --white:#fff;
}
*{box-sizing:border-box;margin:0;padding:0}
html,body{width:1200px;height:4018px;overflow:hidden}
body{position:relative;background:var(--white);font-family:"Open Sans",Arial,sans-serif;color:var(--ink);font-size:13px}
.abs{position:absolute}
.head-font{font-family:"Rajdhani","Arial Narrow",sans-serif}

/* header */
.topbar{left:0;top:0;width:1200px;height:80px;background:var(--white)}
.brand{display:flex;align-items:center;gap:10px}
.brand .mark{width:22px;height:22px;background:var(--red)}
.brand .name{font-family:"Rajdhani",sans-serif;font-weight:700;font-size:36px;color:var(--black);letter-spacing:1px}
.brand-tag{font-size:11px;color:var(--muted);font-weight:600}
.phone-block{right:0;top:0;width:250px;height:80px}
.phone-text{font-family:"Rajdhani",sans-serif;font-weight:700;color:var(--white);line-height:1}
.navbar{left:0;top:80px;width:1200px;height:54px;background:var(--nav)}
.nav-item{position:absolute;top:0;height:54px;line-height:54px;font-size:11px;font-weight:700;text-transform:uppercase;color:#555}
.nav-item.active{background:var(--red);color:var(--white);padding:0 22px}

/* hero */
.hero{left:0;top:134px;width:1200px;height:595px;background:linear-gradient(160deg,#0f1e33 0%,#1f3d63 45%,#0d1a2c 100%)}
.hero-title{top:124px;width:1200px;text-align:center;font-family:"Rajdhani",sans-serif;font-weight:700;font-size:44px;color:var(--white);letter-spacing:.5px}
.hero-sub{width:1200px;text-align:center;font-family:"Rajdhani",sans-serif;font-weight:700;color:var(--white)}
.hero-sub .hl{color:var(--red)}
.btn{display:inline-block;background:var(--red);color:var(--white);font-family:"Rajdhani",sans-serif;font-weight:700;text-transform:uppercase;text-align:center}
.hero-btn{left:496px;top:327px;width:209px;height:46px;line-height:46px;font-size:16px}
.slide-arrow{top:260px;width:30px;height:66px;background:rgba(0,0,0,.45)}
.dots{left:568px;top:530px;display:flex;gap:12px}
.dots span{width:16px;height:16px;border-radius:50%;background:#dcdcdc}
.dots span.on{background:var(--red)}

/* tabs */
.tabs{top:757px;left:0;width:1200px;display:flex;justify-content:center;gap:44px;font-size:11px;font-weight:600;text-transform:uppercase;color:#666}
.tabs .on{color:var(--red);border-bottom:2px solid var(--red);padding-bottom:4px}
.tab-rule{left:402px;top:804px;width:536px;height:1px;background:var(--line)}

/* services */
.svc-label{display:flex;align-items:flex-end;gap:4px;font-family:"Rajdhani",sans-serif;color:var(--black)}
.svc-label .num{font-size:40px;font-weight:500;line-height:.85}
.svc-label .txt{font-size:16px;font-weight:600;text-transform:uppercase;border-bottom:1px solid var(--black);line-height:1.1}
.svc-photo{position:absolute}
.learn-btn{left:95px;top:72px;width:105px;height:32px;line-height:32px;font-size:12px}

/* section titles */
.sec-title{width:1200px;left:0;text-align:center;font-family:"Rajdhani",sans-serif;font-weight:700;font-size:34px;color:var(--black);text-transform:uppercase}
.sec-title .hl{color:var(--red)}
.sec-title.light{color:var(--white)}
.title-rule{height:3px;background:var(--red);width:50px;left:575px}

/* about */
.about-head{left:160px;top:1545px;width:230px;font-family:"Rajdhani",sans-serif;font-weight:700;font-size:19px;line-height:1.25;text-transform:uppercase;color:var(--black)}
.about-copy{left:160px;top:1603px;width:245px;font-size:11.5px;line-height:1.75;color:#555}
.read-btn{left:160px;top:1791px;width:118px;height:30px;line-height:30px;font-size:12px}
.spec-head{left:508px;top:1545px;width:190px;font-family:"Rajdhani",sans-serif;font-weight:700;font-size:16px;line-height:1.25;text-transform:uppercase;color:var(--black)}
.spec-list{left:508px;top:1600px;list-style:none}
.spec-list li{height:56px;font-size:11px;color:#444;display:flex;flex-direction:column;justify-content:flex-end}
.spec-list svg{margin-bottom:4px}
.about-divider{left:706px;top:1548px;width:1px;height:268px;background:var(--line)}

/* why */
.why-band{left:0;top:1891px;width:1200px;height:445px;background:var(--panel)}
.why-photo{left:0;top:1891px;width:590px;height:445px;background:linear-gradient(180deg,#6f9fc4 0%,#9cb8cc 45%,#55606a 100%)}
.why-title{left:638px;top:1922px;font-family:"Rajdhani",sans-serif;font-weight:700;font-size:24px;color:var(--black);text-transform:uppercase}
.why-copy{left:638px;top:1962px;width:410px;font-size:11.5px;line-height:1.7;color:#555}
.why-list{left:638px;top:2063px;width:402px;background:var(--white);border:1px solid var(--line);list-style:none}
.why-list li{position:relative;border-bottom:1px solid var(--line);padding:9px 40px 9px 12px;font-size:14px;color:var(--black)}
.why-list li:last-child{border-bottom:0}
.why-list li::after{content:"";position:absolute;right:14px;top:12px;width:14px;height:14px;border-radius:50%;background:var(--red)}
.why-list li small{display:block;font-size:10px;line-height:1.5;color:#666;margin-top:5px}

/* projects */
.card{border:1px solid var(--line);background:var(--white)}
.card-img{position:absolute;left:0;top:0;width:100%;height:255px}
.card-body{position:absolute;left:18px;top:270px}
.card-body h3{font-family:"Rajdhani",sans-serif;font-weight:700;font-size:16px;text-transform:uppercase;color:var(--black)}
.card-body p{font-size:9px;color:var(--muted)}
.card-zoom{position:absolute;right:14px;top:205px}

/* testimonial */
.testi-band{left:0;top:2920px;width:1200px;height:509px;background:linear-gradient(180deg,#2a2a2c,#1a1a1b)}
.testi-card{background:var(--white);width:410px;height:241px;top:3081px;text-align:center}
.testi-logo{position:absolute;left:130px;top:-40px;width:150px;height:88px;background:var(--white);border:2px solid var(--red);display:flex;align-items:center;justify-content:center;font-weight:700;font-size:15px;color:var(--black)}
.testi-name{position:absolute;top:60px;width:100%;font-size:12px;font-weight:700;text-transform:uppercase;color:var(--black)}
.testi-role{position:absolute;top:77px;width:100%;font-size:9.5px;line-height:1.4;color:#666}
.testi-quote{position:absolute;left:30px;top:118px;width:350px;text-align:left;font-size:10px;line-height:1.6;color:#444;padding-left:20px}
.testi-quote::before{content:"\201C";position:absolute;left:0;top:-6px;font-size:26px;font-weight:700;color:var(--black)}
.testi-close{position:absolute;left:0;top:195px;width:100%;font-size:26px;font-weight:700;color:var(--black)}
.pager{top:3355px;width:29px;height:29px;display:flex;align-items:center;justify-content:center}

/* clients */
.clients-band{left:0;top:3429px;width:1200px;height:295px;background:#e8e8e8}
.client{top:3563px;width:178px;height:102px;display:flex;align-items:center;justify-content:center;font-weight:700;font-size:16px;text-align:center;padding:0 10px}

/* footer */
.footer{left:0;top:3724px;width:1200px;height:294px;background:var(--dark);color:#ccc}
.foot-head{font-family:"Rajdhani",sans-serif;font-weight:700;font-size:19px;color:var(--white)}
.foot-links{list-style:none;font-size:11.5px;line-height:1.6;color:var(--white)}
.foot-links li::before{content:"› ";color:var(--red)}
.foot-rule{left:0;top:3955px;width:1200px;height:1px;background:#44474d}
.copyright{top:3978px;width:1200px;text-align:center;font-size:11px;color:#ccc}
.copyright .hl{color:var(--red)}
</style>
</head>
<body>

<!-- Header -->
<header>
  <div class="abs topbar">
    <div class="abs" style="left:160px;top:10px">
      <div class="brand"><span class="mark"></span><span class="name">VARNO</span></div>
      <div class="brand-tag">Spark Every Day</div>
    </div>
    <svg class="abs phone-block" viewBox="0 0 250 80" width="250" height="80" aria-hidden="true">
      <polygon points="0,0 250,0 250,80 40,80" fill="#d9d9d9"/>
      <polygon points="22,0 250,0 250,80 58,80" fill="#1c1c1e"/>
    </svg>
    <div class="abs" style="right:22px;top:18px;display:flex;align-items:center;gap:10px">
      <svg width="36" height="36" viewBox="0 0 24 24" aria-hidden="true"><path fill="#fff" d="M6.6 10.8a15 15 0 0 0 6.6 6.6l2.2-2.2c.3-.3.7-.4 1-.2 1.1.4 2.3.6 3.6.6.6 0 1 .4 1 1V20c0 .6-.4 1-1 1A17 17 0 0 1 3 4c0-.6.4-1 1-1h3.5c.6 0 1 .4 1 1 0 1.3.2 2.5.6 3.6.1.3 0 .7-.2 1z"/></svg>
      <div class="phone-text"><div style="font-size:34px">13 <span style="color:var(--red)">8276</span></div><div style="font-size:15px;letter-spacing:4px;text-align:right">VARNO</div></div>
    </div>
  </div>
  <nav class="abs navbar">
    <span class="nav-item active" style="left:166px">Home</span>
    <span class="nav-item" style="left:252px">Varno Story</span>
    <span class="nav-item" style="left:330px">Our Works</span>
    <span class="nav-item" style="left:408px">Contact Us</span>
    <span class="nav-item" style="left:815px">Electrical</span>
    <span class="nav-item" style="left:888px">LED Lighting</span>
    <span class="nav-item" style="left:972px">Solar Power</span>
  </nav>
</header>

<!-- Hero -->
<section class="abs hero" role="img" aria-label="Photograph of high-voltage power lines against a dusk sky">
  <h1 class="abs hero-title">WE ARE BIG POWERFUL AND RELIABLE</h1>
  <p class="abs hero-sub" style="top:176px;font-size:20px"><span class="hl">VARNO</span> provides electrical energy led lighting and solar power energy solutions from a decades</p>
  <p class="abs hero-sub" style="top:212px;font-size:23px">We impartially compare all of these suppliers and more</p>
  <a class="abs btn hero-btn">Switch Now</a>
  <div class="abs slide-arrow" style="left:0"></div>
  <div class="abs slide-arrow" style="right:0">
    <svg width="30" height="66" viewBox="0 0 30 66" aria-hidden="true"><path d="M12 27l7 6-7 6" stroke="#fff" stroke-width="2" fill="none"/></svg>
  </div>
  <div class="abs dots"><span></span><span></span><span class="on"></span></div>
</section>

<!-- Service tabs -->
<div class="abs tabs"><span>Electrical</span><span class="on">LED Lighting</span><span>Solar Power &amp; Storage</span></div>
<div class="abs tab-rule"></div>

<!-- Services -->
<section>
  <div class="abs svc-label" style="left:190px;top:838px"><span class="num">01</span><span class="txt">Electrical</span></div>
  <div class="svc-photo" style="left:160px;top:882px;width:295px;height:171px;background:linear-gradient(135deg,#c33 0%,#e0c24a 40%,#6b4a3a 100%)" role="img" aria-label="Photograph of a multimeter testing wiring"></div>

  <div class="abs svc-label" style="left:490px;top:1008px"><span class="num">02</span><span class="txt">LED Lighting</span></div>
  <div class="svc-photo" style="left:455px;top:1053px;width:295px;height:174px;background:radial-gradient(circle at 50% 45%,#5b5b55 0%,#1e2328 60%,#111 100%)" role="img" aria-label="Photograph of hanging LED bulbs in a dark room">
    <a class="abs btn learn-btn">Learn More</a>
  </div>

  <div class="abs svc-label" style="left:790px;top:1172px"><span class="num">03</span><span class="txt">Solar Power &amp; Storage</span></div>
  <div class="svc-photo" style="left:750px;top:1224px;width:290px;height:172px;background:linear-gradient(180deg,#3d7fd0 0%,#9cc4ea 55%,#3c5a86 100%)" role="img" aria-label="Photograph of wind turbines and solar panels under a blue sky"></div>
</section>

<!-- About -->
<section>
  <h2 class="abs sec-title" style="top:1440px">About <span class="hl">Varno</span></h2>
  <div class="abs title-rule" style="top:1484px;left:568px"></div>

  <h3 class="abs about-head">We take action more<br><span style="color:#555">than speak</span></h3>
  <p class="abs about-copy">Varno Electrical was formed to be an expert Electricity Contracting Company providing services to all Residential and Commercial Customers. With over 10 years of experience, Varno Electrical has developed a highly-experienced team of professionals that ensure all our customer expectations are met.</p>
  <a class="abs btn read-btn">Read More</a>

  <h3 class="abs spec-head">Varno Electrical<br>specialise in:</h3>
  <ul class="abs spec-list">
    <li><svg width="22" height="18" viewBox="0 0 22 18" aria-hidden="true"><path d="M12 1L5 10h5l-2 7 8-10h-5l2-6z" fill="none" stroke="#888" stroke-width="1.3"/></svg>Electrical Contracting</li>
    <li><svg width="22" height="20" viewBox="0 0 22 20" aria-hidden="true"><circle cx="11" cy="8" r="6" fill="none" stroke="#888" stroke-width="1.3"/><path d="M8 15h6M9 18h4" stroke="#888" stroke-width="1.3"/></svg>LED Lighting Upgrades</li>
    <li><svg width="22" height="20" viewBox="0 0 22 20" aria-hidden="true"><rect x="2" y="3" width="16" height="14" fill="none" stroke="#888" stroke-width="1.3"/><path d="M2 10h16M10 3v14" stroke="#888" stroke-width="1.3"/></svg>Solar Power</li>
    <li><svg width="22" height="20" viewBox="0 0 22 20" aria-hidden="true"><path d="M11 2l7 3v5c0 4-3 7-7 8-4-1-7-4-7-8V5z" fill="none" stroke="#888" stroke-width="1.3"/></svg>Security Systems</li>
  </ul>
  <div class="abs about-divider"></div>
  <div class="abs" style="left:723px;top:1548px;width:317px;height:268px;background:linear-gradient(180deg,#efefef 0%,#e3e3e3 62%,#7a4f30 63%,#5b3820 100%)" role="img" aria-label="Photograph of a bright lounge room with pendant lights and timber floor"></div>
</section>

<!-- Why choose us -->
<section>
  <div class="abs why-band"></div>
  <div class="abs why-photo" role="img" aria-label="Photograph of two electricians shaking hands near a substation"></div>
  <h2 class="abs why-title">Why chose us?</h2>
  <p class="abs why-copy">Quality, Reliability and Customer First – these are the key foundations that we offer our customers. All work is covered by a 5 year workmanship warranty and a minimum 1 year warranty on all products</p>
  <ul class="abs why-list">
    <li>Professional service<small>When you hire a Varno Electrical Electrician you will get a professional and well-presented Electrician that comes skilled and ready to do the job.</small></li>
    <li>5-year workmanship guarantee</li>
    <li>Value for Money</li>
    <li>Environmentally friendly</li>
    <li>Fully insured</li>
  </ul>
</section>

<!-- Recent projects -->
<section>
  <h2 class="abs sec-title" style="top:2402px">Our Recent Project</h2>
  <div class="abs title-rule" style="top:2446px"></div>

  <article class="abs card" style="left:72px;top:2505px;width:333px;height:329px">
    <div class="card-img" style="background:linear-gradient(180deg,#f4f4f4 0%,#f4f4f4 28%,#8a8d90 29%,#4d5155 100%)" role="img" aria-label="Photograph of a signage workshop interior"></div>
    <svg class="card-zoom" width="40" height="40" viewBox="0 0 40 40" aria-hidden="true"><circle cx="17" cy="17" r="12" fill="#fff" stroke="#333" stroke-width="3"/><path d="M26 26l10 10" stroke="#333" stroke-width="4"/><path d="M12 17h10M17 12v10" stroke="#333" stroke-width="2"/></svg>
    <div class="card-body"><h3>Outlet Power Management</h3><p>Aug 2016</p></div>
  </article>

  <article class="abs card" style="left:434px;top:2505px;width:332px;height:329px">
    <div class="card-img" style="background:linear-gradient(180deg,#f4f4f4 0%,#f4f4f4 28%,#9a9ea3 29%,#5c6167 100%)" role="img" aria-label="Photograph of a steel warehouse with new LED fittings"></div>
    <svg class="card-zoom" width="40" height="40" viewBox="0 0 40 40" aria-hidden="true"><circle cx="17" cy="17" r="12" fill="#fff" stroke="#333" stroke-width="3"/><path d="M26 26l10 10" stroke="#333" stroke-width="4"/><path d="M12 17h10M17 12v10" stroke="#333" stroke-width="2"/></svg>
    <div class="card-body"><h3>LED Integration</h3><p>Aug 2016</p></div>
  </article>

  <article class="abs card" style="left:796px;top:2505px;width:332px;height:329px">
    <div class="card-img" style="background:linear-gradient(180deg,#3a3c3f,#5a5c5f)" role="img" aria-label="Photograph of a retail shopfront at night"></div>
    <svg class="abs" style="left:146px;top:108px" width="40" height="40" viewBox="0 0 40 40" aria-hidden="true"><circle cx="20" cy="20" r="19" fill="#ec1f27"/><path d="M11 20h18M20 11v18" stroke="#fff" stroke-width="3"/></svg>
    <div class="card-body"><h3>Electricity Installation</h3><p>Aug 2016</p></div>
  </article>
</section>

<!-- Testimonials -->
<section>
  <div class="abs testi-band" role="img" aria-label="Dark photograph of electrical wiring behind the testimonials"></div>
  <h2 class="abs sec-title light" style="top:2958px">Client Testimonial</h2>
  <div class="abs title-rule" style="top:3002px"></div>

  <article class="abs testi-card" style="left:161px">
    <div class="testi-logo">Outback Supply Co</div>
    <div class="testi-name">Jordan Pell</div>
    <div class="testi-role">Executive<br>Outback Supply Co</div>
    <p class="testi-quote">The praise, commercial and attention to service of Varno Electrical has been awesome. We would strongly recommend them to any business contemplating upgrading their lighting or any other electrical work.</p>
    <div class="testi-close">&#8221;</div>
  </article>

  <article class="abs testi-card" style="left:630px">
    <div class="testi-logo">Velvetline</div>
    <div class="testi-name">R. Calder</div>
    <div class="testi-role">Clayton North VIC</div>
    <p class="testi-quote">They show up after the job, explained everything I needed to know and answered all questions, very professional. Will ask them again in the future.</p>
    <div class="testi-close">&#8221;</div>
  </article>

  <div class="abs pager" style="left:563px;background:#d8d8d8"><svg width="10" height="14" viewBox="0 0 10 14" aria-hidden="true"><path d="M7 2L2 7l5 5" stroke="#555" stroke-width="2" fill="none"/></svg></div>
  <div class="abs pager" style="left:605px;background:var(--red)"><svg width="10" height="14" viewBox="0 0 10 14" aria-hidden="true"><path d="M3 2l5 5-5 5" stroke="#fff" stroke-width="2" fill="none"/></svg></div>
</section>

<!-- Clients -->
<section>
  <div class="abs clients-band"></div>
  <h2 class="abs sec-title" style="top:3474px;font-size:24px">Our Satisfied Clients Include</h2>
  <div class="abs title-rule" style="top:3508px"></div>
  <div class="abs client" style="left:160px;background:#fff;color:#333">Velvetline</div>
  <div class="abs client" style="left:394px;background:#9a9a9a;color:#222">Outback Supply Co</div>
  <div class="abs client" style="left:627px;background:#6a6a6a;color:#fff">Heron Plumbing Supplies</div>
  <div class="abs client" style="left:863px;background:#555;color:#fff">Burgerhaus</div>
</section>

<!-- Footer -->
<footer class="abs footer">
  <div class="abs" style="left:225px;top:22px">
    <div class="brand"><span class="mark"></span><span class="name" style="color:#fff;font-size:32px">VARNO</span></div>
  </div>
  <div class="abs phone-text" style="left:225px;top:78px;display:flex;align-items:center;gap:8px">
    <svg width="28" height="28" viewBox="0 0 24 24" aria-hidden="true"><path fill="#fff" d="M6.6 10.8a15 15 0 0 0 6.6 6.6l2.2-2.2c.3-.3.7-.4 1-.2 1.1.4 2.3.6 3.6.6.6 0 1 .4 1 1V20c0 .6-.4 1-1 1A17 17 0 0 1 3 4c0-.6.4-1 1-1h3.5c.6 0 1 .4 1 1 0 1.3.2 2.5.6 3.6.1.3 0 .7-.2 1z"/></svg>
    <div><div style="font-size:26px">13 <span style="color:var(--red)">8276</span></div><div style="font-size:12px;letter-spacing:3px">VARNO</div></div>
  </div>
  <div class="abs" style="left:225px;top:136px;display:flex;gap:8px">
    <span style="width:26px;height:26px;border-radius:50%;background:#3b5ba0"></span>
    <span style="width:26px;height:26px;border-radius:50%;background:#fff"></span>
    <span style="width:26px;height:26px;border-radius:50%;background:#fff"></span>
  </div>

  <div class="abs" style="left:528px;top:48px">
    <div class="foot-head" style="border-bottom:2px solid var(--red);padding-bottom:2px">Some Quick Links</div>
    <ul class="foot-links" style="margin-top:12px">
      <li>LED Lighting</li><li>Solar Power</li><li>Electrical</li><li>Career</li>
    </ul>
  </div>

  <div class="abs" style="left:850px;top:52px">
    <div class="foot-head">Other</div>
    <div style="margin-top:12px;font-size:11.5px;line-height:1.6;color:#fff">Terms and Conditions<br>Privacy and policy</div>
    <div style="display:flex;gap:5px;margin-top:6px">
      <span style="width:42px;height:14px;background:#4a67a8;border-radius:2px"></span>
      <span style="width:26px;height:14px;background:#ddd;border-radius:2px"></span>
      <span style="width:38px;height:14px;background:#4a67a8;border-radius:2px"></span>
      <span style="width:50px;height:14px;background:#3d8fd0;border-radius:2px"></span>
    </div>
  </div>

  <div class="abs foot-rule" style="top:231px"></div>
  <p class="abs copyright" style="top:254px">© <span class="hl">Varno</span> | Technologies | All rights reserved 2017</p>
</footer>

</body>
</html>
```